Professional & attention grabbing.

A business card design, front and back. I already have a logo I will attach, but I am open to something new as well.
Things to include:
Name:
Title:
Phone:
Email:
Wanting something that is professional but attention grabbing.
Also we do a lot of work using drones on natural gas pipelines (leading the future)if you want to include any of that. I'm open to ideas.
Target Market(s)
Natural gas transmission industry / greenhouse gas mitigation industry
Industry/Entity Type
Business
Colors
Designer to choose colors to be used in the design.
Look and feel
Each slider illustrates characteristics of the customer's brand and the style your logo design should communicate.

```html
<!DOCTYPE html>
<html lang="en">
<head>
<meta charset="utf-8">
<title>Kestrel Field – Business Card</title>
<link href="https://fonts.googleapis.com/css2?family=Arimo:wght@400;700&display=swap" rel="stylesheet">
<style>
  :root {
    --backdrop: #3b3230;
    --card: #141414;
    --card-edge: #1d1d1d;
    --silver: #8e8e8e;
    --silver-dim: #5c5c5c;
    --red: #c8202a;
    --white: #f2f2f2;
    --rule: #6a6a6a;
  }
  * { box-sizing: border-box; margin: 0; padding: 0; }
  html, body {
    width: 1200px; height: 864px; overflow: hidden;
    background: var(--backdrop);
    font-family: "Arimo", Arial, sans-serif;
  }
  .canvas {
    width: 1200px; height: 864px;
    display: flex; align-items: center; justify-content: center; gap: 40px;
  }
  .card {
    width: 540px; height: 309px;
    background: var(--card);
    border: 1px solid var(--card-edge);
    position: relative;
    box-shadow: 0 10px 30px rgba(0,0,0,.45);
  }
  /* Back side */
  .card-back .brand {
    position: absolute; left: 70px; top: 92px;
    display: flex; align-items: center; gap: 16px;
  }
  .brand-square {
    width: 62px; height: 62px; background: var(--silver);
  }
  .card-back .brand-name {
    font-weight: 700; font-size: 40px; letter-spacing: 1px;
    color: var(--silver); text-transform: uppercase; line-height: 1;
  }
  .card-back .web {
    position: absolute; left: 70px; top: 200px;
    font-size: 13px; letter-spacing: 6px; color: var(--silver-dim);
  }
  /* Front side */
  .card-front .brand {
    position: absolute; left: 60px; top: 110px;
    display: flex; flex-direction: column; align-items: flex-start; gap: 10px;
  }
  .card-front .brand-square { width: 56px; height: 56px; background: var(--red); }
  .card-front .brand-name {
    font-weight: 700; font-size: 20px; color: var(--white);
    text-transform: uppercase; letter-spacing: 1px;
  }
  .divider {
    position: absolute; left: 250px; top: 90px;
    width: 1px; height: 130px;
    background: linear-gradient(to bottom, transparent, var(--rule), transparent);
  }
  .contact { position: absolute; left: 272px; top: 110px; }
  .person-name { font-size: 17px; color: var(--red); line-height: 1.1; }
  .person-title { font-size: 15px; color: var(--white); margin-bottom: 12px; }
  .contact-list { list-style: none; }
  .contact-list li {
    display: flex; align-items: center; gap: 10px;
    font-size: 13px; color: var(--white); line-height: 20px;
  }
  .contact-list svg { width: 12px; height: 12px; fill: var(--red); flex: none; }
</style>
</head>
<body>
<main class="canvas">
  <section class="card card-back" aria-label="Card back">
    <div class="brand">
      <span class="brand-square"></span>
      <span class="brand-name">Kestrel Field</span>
    </div>
    <p class="web">www.kestrelfield.com</p>
  </section>

  <section class="card card-front" aria-label="Card front">
    <div class="brand">
      <span class="brand-square"></span>
      <span class="brand-name">Kestrel Field</span>
    </div>
    <span class="divider"></span>
    <div class="contact">
      <p class="person-name">Mara Lind</p>
      <p class="person-title">President</p>
      <ul class="contact-list">
        <li>
          <svg viewBox="0 0 24 24" aria-hidden="true"><path d="M6.6 10.8a15 15 0 0 0 6.6 6.6l2.2-2.2a1 1 0 0 1 1-.25 11.4 11.4 0 0 0 3.6.57 1 1 0 0 1 1 1V20a1 1 0 0 1-1 1A17 17 0 0 1 3 4a1 1 0 0 1 1-1h3.5a1 1 0 0 1 1 1c0 1.25.2 2.45.57 3.57a1 1 0 0 1-.25 1z"/></svg>
          555 0142 7781
        </li>
        <li>
          <svg viewBox="0 0 24 24" aria-hidden="true"><path d="M2 5h20v14H2z M2 5l10 8 10-8" /></svg>
          mara@kestrelfield.com
        </li>
        <li>
          <svg viewBox="0 0 24 24" aria-hidden="true"><circle cx="12" cy="12" r="10"/></svg>
          www.kestrelfield.com
        </li>
      </ul>
    </div>
  </section>
</main>
</body>
</html>
```